2-Page Flyer for the Information Session about the Quiet Pathfinder Course

This is a flyer to announce/advertise an evening Information Session about the Quiet Pathfinder Course. This Program aims at mindfully rethinking and redesigning work (and life) for people who feel stuck or not entirely satisfied with their work and/or life (please see draft flyer attached for more details). This Program is property of Bright Meadow, a company that uses a combination of Mindfulness, Design, and Entrepreneurship to help people achieve greater happiness (in their work and lives).

Target Market(s)

People who feel stuck or not entirely satisfied with their work and/or life (please see draft flyer attached for more details)

Font styles to use
Serif
Sans Serif

Colors
ffffff
f37122
33a6d7
acd037

Requirements
Must have
• All of what I will say below is suggestive (I’m not a design expert), and I’m open to divert from it, if it makes sense and feels more interesting.
• I thought initially of a 2-page flyer (please see draft flyer attached). The first page could help people grasp the essence of the event quickly (in 1 or 2 minutes), and then, if they are interested/motivated, they would continue reading through page 2, which has more info about the Program in itself.
• Potential Structure
• Page 1
• . About the Information Session on the Quiet Pathfinder Course
• . Visible Date & Time, Contacts, Venue (and other relevant info)
• . About me (the facilitator)
• Page 2
• . About the Quiet Pathfinder Course
• I include a Powerpoint draft of the flyer with the content. The design is rudimentary and precarious from an aesthetics/organization point of view, and this is mainly where I need help (and maybe in other aspects too!).
• On the flyer, I would like to include:
• . A photo of myself (I attach 1 picture).
• . 1 or 2 beautiful-nature photos (cropped or full). One may have to do with looking at the sky, dreaming, and imagining a new work and life (2 photos with sky and clouds attached). The other has to do with walking the transformation journey (the photo with the person walking through the forest path).
• . bright meadow logo or logos (there are two slightly different ones, that can be used for different purposes). For the first page, I would like the bright meadow logo that has "bright meadow" written on the bottom, with the saying "Stillness, Craft and Venture for Bright Meadow" beneath. This is the main logo. For the 2nd page, you can choose the logo that adapts better.
• - Where it says the "the way out is in" it would be great to have a similar font to the one I attach (see file "Font_the_way_out_is_in.png" and Ankecallig-fg.ttf
Nice to have
• In terms of colours, I would not divert much from the logo colours (and of course white and black). I would like the flyer to be quite white. Almost like fairy-tale white: the white horse, the white snow, the white of the stars, the white heaven. White could be the base colour. White means peace, tranquillity, calm contentment, a smile.
• And then use the other colours. The green of the mindfulness. The blue of the sky, the dreams. And the orange of the sun, the energy, the fire, the action. And maybe the black for text.
• Where it says the "the way out is in" it would be great to have a similar font to the one I attach (see file "Font_the_way_out_is_in".
• I would like this flyer to be a piece of art, in every possible way. Simple, beautiful, ease, light, peaceful, calm happy. Just like the Quiet Pathfinder Course and bright meadow Company that I am creating intends to be. The mission of this Program and Company is to be a designer, a painter (a Picasso) of happier and more fulfilling human lives.
• I am very much looking forward to seeing your proposal(s).

```html
<!DOCTYPE html>
<html lang="en">
<head>
<meta charset="utf-8">
<title>Quiet Pathfinder Course – Information Session Flyer</title>
<link href="https://fonts.googleapis.com/css2?family=Oswald:wght@600;700&family=Questrial&family=Libre+Baskerville:ital,wght@0,400;0,700;1,400&family=Great+Vibes&display=swap" rel="stylesheet">
<style>
  :root{
    --white:#ffffff;
    --orange:#f37122;
    --blue:#33a6d7;
    --sky:#4fc8ea;
    --green:#acd037;
    --lime:#9fe01a;
    --grey:#c9cccd;
    --ink:#1c1c1c;
    --line:#222;
  }
  *{box-sizing:border-box;margin:0;padding:0}
  html,body{width:1200px;height:849px;overflow:hidden;background:var(--white)}
  body{position:relative;font-family:"Questrial",sans-serif;color:var(--ink)}
  .page{position:absolute;top:20px;width:547px;height:789px;border:1px solid var(--line);background:var(--white);overflow:hidden}
  .page--front{left:31px}
  .page--back{left:622px}
  .abs{position:absolute}
  .sheet-label{position:absolute;top:818px;font-size:14px;letter-spacing:.5px;color:#333}
  .serif{font-family:"Libre Baskerville",serif}
  .sans{font-family:"Questrial",sans-serif}
  .display{font-family:"Oswald",sans-serif;font-weight:700}
  .body-text{font-size:11.4px;line-height:14.6px}

  /* front */
  .sky-photo{left:-140px;top:-12px;width:282px;height:282px;border-radius:50%;background:radial-gradient(circle at 60% 35%,#dff1fb 0%,#8fc6e6 38%,#5f9a74 62%,#3d6b4d 100%)}
  .sky-photo--small{left:82px;top:14px;width:158px;height:158px;border-radius:50%;background:radial-gradient(circle at 50% 45%,#eef7fc,#a8d2ec 70%,#7fb3d6)}
  .brand-dot{left:360px;top:16px;width:44px;height:44px;border-radius:50%;background:var(--blue)}
  .brand-name{left:240px;width:283px;top:74px;text-align:center;font-size:21px;line-height:25px;color:var(--orange)}
  .brand-tagline{left:240px;width:283px;top:103px;text-align:center;font-size:11px;line-height:14px;white-space:nowrap}
  .course-title{left:240px;width:283px;top:131px;text-align:center;font-size:27px;line-height:31px;letter-spacing:.3px}
  .session-box{left:240px;top:203px;width:283px;height:43px;border:1.5px solid var(--orange);display:flex;align-items:center;justify-content:center;font-size:24px;color:var(--orange)}
  .session-date{left:236px;width:291px;top:254px;text-align:center;font-size:12.6px;line-height:16px;white-space:nowrap}
  .band{left:0;display:flex;align-items:center;padding-left:22px;color:var(--white);font-size:15.5px;white-space:nowrap;font-weight:400}
  .band--orange{top:294px;width:203px;height:32px;background:var(--orange)}
  .band--blue{top:374px;width:284px;height:33px;background:var(--sky)}
  .band--green{top:484px;width:284px;height:40px;background:var(--green);display:block;padding-top:7px;font-size:12px;line-height:14px}
  .band-sub{display:block;text-align:right;padding-right:14px;font-size:8px;line-height:10px;margin-top:1px}
  .text-session{left:22px;top:332px;width:510px}
  .text-who{left:22px;top:415px;width:515px}
  .bio{left:22px;top:534px;width:322px;font-size:11px;line-height:13.3px}
  .more-link{left:22px;top:701px;font-size:10.5px;font-style:italic}
  .more-link a{color:var(--blue);text-decoration:none;font-style:normal}
  .portrait{border-radius:50%;background:linear-gradient(150deg,#e9e9e9,#9d9d9d)}
  .portrait--a{left:320px;top:477px;width:123px;height:123px;border:2px solid var(--blue)}
  .portrait--b{left:401px;top:495px;width:131px;height:131px;border:2.5px solid var(--orange);background:linear-gradient(150deg,#d8d8d8,#4a4a4a)}
  .portrait--c{left:355px;top:580px;width:132px;height:132px;border:2.5px solid var(--green);background:linear-gradient(150deg,#f1f1f1,#a89a8e)}
  .rule{left:21px;top:733px;width:492px;height:1px;background:var(--line)}
  .footer{font-size:8.8px;line-height:14px;white-space:nowrap}
  .footer b{font-weight:700}
  .footer i{font-style:italic}
  .footer--left{left:21px;top:748px}
  .footer--right{left:335px;top:748px}

  /* back */
  .back-dot{left:24px;top:13px;width:34px;height:34px;border-radius:50%;background:var(--blue)}
  .back-brand{left:66px;top:13px;font-size:14px;line-height:14px;color:var(--orange)}
  .green-band{left:0;top:52px;width:547px;height:150px;background:var(--lime)}
  .forest-photo{left:332px;top:12px;width:215px;height:212px;border-radius:40% 8% 30% 45%;background:linear-gradient(180deg,#6b5a3e 0%,#4d5a2e 45%,#7d9a3a 75%,#b7c46a 100%)}
  .what-title{left:23px;top:60px;font-size:15.5px;line-height:20px;white-space:nowrap}
  .what-title b{font-weight:700}
  .what-text{left:23px;top:84px;width:305px;color:var(--white);font-size:11.6px;line-height:14.6px}
  .what-text span{color:var(--ink)}
  .side-tab{left:0;width:42px;display:flex;align-items:center;justify-content:center;color:var(--white)}
  .side-tab span{transform:rotate(-90deg);white-space:nowrap;font-size:26px;letter-spacing:.5px}
  .side-tab--program{top:218px;height:169px;background:var(--orange)}
  .side-tab--why{top:404px;height:117px;background:var(--sky)}
  .side-tab--how{top:537px;height:101px;background:var(--green)}
  .program-text{left:54px;top:224px;width:265px;font-size:11.2px;line-height:14.1px}
  .why-text{left:54px;top:405px;width:490px;font-size:11.2px;line-height:14.1px}
  .how-text{left:54px;top:537px;width:490px;font-size:11.2px;line-height:14.1px}
  .indent{padding-left:30px;display:block}
  .cycle{left:320px;top:225px;width:227px;height:170px}
  .mountain-band{left:12px;top:658px;width:519px;height:73px;border-radius:30px 8px 26px 12px;background:linear-gradient(180deg,#dbe7ef 0%,#8fb1c4 45%,#5e8a6b 100%)}
  .motto{left:12px;top:655px;width:519px;text-align:center;font-family:"Great Vibes",cursive;font-size:31px;line-height:36px;color:var(--white)}
  .back-footer{font-size:9px;line-height:14px;white-space:nowrap}
  .back-footer--left{left:27px;top:748px}
  .back-footer--right{left:326px;top:748px}
</style>
</head>
<body>

<section class="page page--front">
  <div class="abs sky-photo" role="img" aria-label="Mountain landscape under a bright sky with clouds, framed in soft circles"></div>
  <div class="abs sky-photo--small" role="img" aria-label="Sky and clouds in a second circle"></div>

  <div class="abs brand-dot"></div>
  <div class="abs brand-name sans">bright meadow</div>
  <p class="abs brand-tagline">Stillness, Craft and Venture for Bright Meadow</p>

  <h1 class="abs course-title display">QUIET PATHFINDER<br>COURSE</h1>
  <div class="abs session-box serif">Information Session</div>
  <p class="abs session-date serif"><b>Thursday 18th July 2019</b>, from <b>19:30 to 21:00</b></p>

  <h2 class="abs band band--orange serif">Information Session:</h2>
  <p class="abs text-session body-text">The purpose of this Information Session is to give you a real insight into the Quiet Pathfinder Course and how it can help you get the most out of your work and life.</p>

  <h2 class="abs band band--blue serif">How much and who can come?</h2>
  <p class="abs text-who body-text">The Information Session is free and whether you come on your own, or with friends or family, you'll be warmly welcome. It will take place on Thursday the 23rd July 2019, from 19:30 to 21:00, at Tide Coworking. Please get in touch for more info or to book a place.</p>

  <h2 class="abs band band--green serif">Facilitator: Dr Marco Vell<span class="band-sub">Visiting Research Fellow, Northfield University</span></h2>
  <p class="abs bio">Marco joined Northfield University (School of Management) as a Lecturer in Entrepreneurship in 2015. He completed his PhD in Entrepreneurship at Ardmore Business School (University of Ardmore) in 2014. His dissertation received the Linden Doctoral Dissertation Award from the Society for Management Studies. Marco began his working career in the semiconductor industry as a production engineer (Corvex), and then in healthcare as a sales engineer (Halden). After his MBA, he worked as a strategy consultant at Douro Business School. Originally from Portugal, Marco enjoys designing and launching new ideas, international communities, stillness retreats, and musical improvisation.</p>
  <p class="abs more-link">More about the facilitator: <a href="#">www.profiles.example/in/marcovell</a></p>

  <div class="abs portrait portrait--a" role="img" aria-label="Portrait photo of the facilitator in a scarf"></div>
  <div class="abs portrait portrait--b" role="img" aria-label="Black and white portrait photo of the facilitator"></div>
  <div class="abs portrait portrait--c" role="img" aria-label="Smiling portrait photo of the facilitator in a checked shirt"></div>

  <div class="abs rule"></div>
  <p class="abs footer footer--left"><b>Information &amp; Booking:</b> <i>Please contact for more information or to book a place</i><br><b>Venue:</b> Tide Coworking, C/ Alzina 12, Barcelona</p>
  <p class="abs footer footer--right"><b>Tel No.:</b> +34 600 410 275 (video call &amp; messaging)<br><b>Email:</b> info@brightmeadow.example</p>
</section>

<section class="page page--back">
  <div class="abs back-dot"></div>
  <div class="abs back-brand sans">bright<br>meadow</div>

  <div class="abs green-band"></div>
  <div class="abs forest-photo" role="img" aria-label="A person walking along a forest path between tall trees"></div>
  <h2 class="abs what-title serif">What is <b>Quiet Pathfinding?</b></h2>
  <p class="abs what-text">Being mindful means being aware and awake. Entrepreneurship is the creation of a new form of organising. <span>Quiet Pathfinding</span> is then the process of creating or redesigning your work and life with awareness, in a way that is reflective of you, of your passions and values, thus conducing to a greater sense of fulfilment and happiness.</p>

  <div class="abs side-tab side-tab--program display"><span>THE PROGRAM</span></div>
  <p class="abs program-text">The <b>Quiet Pathfinder Course</b> is a 4-month long transformative journey for people who feel stuck or not entirely satisfied with their work and/or life. It will be of benefit for everyone, at any stage.<br>The Program consists of a series of four 5-hour workshops, one per month, complemented by 2-hour weekly peer support meetings.<br>It combines mindfulness techniques, design thinking methodology and entrepreneurship frameworks to achieve the desired outcomes.</p>

  <svg class="abs cycle" viewBox="0 0 227 170" aria-label="Cycle of four workshops linked by weekly peer support meetings">
    <g fill="none" stroke-width="3">
      <path d="M70 52 L58 64" stroke="#dfe3e4"/>
      <path d="M128 52 L138 64" stroke="#c9ec8a"/>
      <path d="M148 118 L136 128" stroke="#9fd3ee"/>
      <path d="M56 114 L68 126" stroke="#f6b48d"/>
    </g>
    <circle cx="99" cy="35" r="27" fill="#9fe01a"/>
    <circle cx="163" cy="88" r="27" fill="#4fb2e3"/>
    <circle cx="99" cy="140" r="27" fill="#f37122"/>
    <circle cx="40" cy="88" r="27" fill="#c9cccd"/>
    <g font-family="Questrial, sans-serif" fill="#fff" text-anchor="middle">
      <text x="99" y="29" font-size="6">Workshop 1</text><text x="99" y="37" font-size="7">-INSIGHT-</text><text x="99" y="44" font-size="5.5" font-style="italic">(5 hours)</text>
      <text x="163" y="82" font-size="6">Workshop 2</text><text x="163" y="90" font-size="7">-DESIGN-</text><text x="163" y="97" font-size="5.5" font-style="italic">(5 hours)</text>
      <text x="99" y="134" font-size="6">Workshop 3</text><text x="99" y="142" font-size="7">-EXECUTE-</text><text x="99" y="149" font-size="5.5" font-style="italic">(5 hours)</text>
      <text x="40" y="82" font-size="6">Workshop 4</text><text x="40" y="90" font-size="7">-PRESENT-</text><text x="40" y="97" font-size="5.5" font-style="italic">(5 hours)</text>
    </g>
    <g font-family="Questrial, sans-serif" fill="#555" font-size="5.8" font-style="italic" text-anchor="middle">
      <text x="36" y="46">WPS meetings</text>
      <text x="198" y="42">Weekly Peer Support</text><text x="198" y="50">(WPS) meetings</text>
      <text x="36" y="140">WPS meetings</text>
      <text x="196" y="140">WPS meetings</text>
    </g>
  </svg>

  <div class="abs side-tab side-tab--why display"><span>WHY</span></div>
  <p class="abs why-text">Many people are not entirely satisfied with their work, but they don't know what to do about it. The <b>Quiet Pathfinder Course</b> offers an opportunity, a safe place, a collective journey to help you reflect, design, and (very likely) do something about it.<br>By the end of the Program, you should have:
    <span class="indent">1) Increased awareness, clarity and confidence</span>
    <span class="indent">2) A deeper insight on what makes you happier and what you want</span>
    <span class="indent">3) A clear design integrating your intended work and life</span>
    <span class="indent">4) Initiated the execution of this design.</span></p>

  <div class="abs side-tab side-tab--how display"><span>HOW</span></div>
  <p class="abs how-text">This Program differs from existing entrepreneurial programs in many ways:
    <span class="indent">1) It starts upstream with mindfulness and self analysis to look deeply into yourself</span>
    <span class="indent">2) Design and execution decisions are rooted on happiness rather than (only) financials</span>
    <span class="indent">3) The process is holistic and inclusive, aiming at designing an integrated work and life,</span>
    and on building synergies between your different parts.<br>The Program format includes lectures, individual work, group sharing, guided activities, experiential exercises, video, audio, handouts and other resources.</p>

  <div class="abs mountain-band" role="img" aria-label="Panoramic view of blue mountain ridges under a pale sky"></div>
  <p class="abs motto">“The Way Out is In”</p>

  <p class="abs back-footer back-footer--left"><b>Date</b>&nbsp;&nbsp;: Thursday 23rd, from 19:30 to 21:00<br><b>Venue:</b>&nbsp; Tide Coworking, C/ Alzina 12, Barcelona</p>
  <p class="abs back-footer back-footer--right"><b>Email</b> : info@brightmeadow.example<br><b>Tel No.:</b> +34 600 410 275 (video call &amp; messaging)</p>
</section>

<div class="sheet-label" style="left:267px">FRONT</div>
<div class="sheet-label" style="left:892px">BACK</div>

</body>
</html>
```